Custom Manufacturing Company square space website design

I own a custom manufacturing company that uses precision cutting technology to manufacture project components over a couple industries. We have an industrial CNC router and state of the art edge bander and cut a lot of cabinetry components for cabinet shops, builders, closet companies, ect. We offer design and assembly for any cabinetry or can build cabinets to spec. We also cut components for other industries out of wood, plastics, acryclics, ect. We offer design engineering services, product development protype services. we have a 3D printer farm. We want our communicate trust, dependability, and the value we place on client relationships.

We essentially want a credibility website. Landing page and drops downs for services we offer, capabilites, about us, contact

```html
<!DOCTYPE html>
<html lang="en">
<head>
<meta charset="utf-8">
<title>Northfield Mill Works — Custom Manufacturing</title>
<link href="https://fonts.googleapis.com/css2?family=Poppins:wght@700;800&family=Mulish:wght@400;600;700&display=swap" rel="stylesheet">
<style>
:root{
  --teal:#17a2c2;
  --ink:#111111;
  --text:#444444;
  --muted:#666666;
  --line:#bdbdbd;
  --soft:#f4f2f2;
  --white:#ffffff;
  --footer:#121212;
}
*{box-sizing:border-box;margin:0;padding:0}
html,body{width:1200px;height:3123px;overflow:hidden}
body{position:relative;background:var(--white);font-family:"Mulish",sans-serif;color:var(--text)}
.abs{position:absolute}
.heading{font-family:"Poppins",sans-serif;font-weight:800;color:var(--ink);text-transform:uppercase;letter-spacing:.5px}
.btn{position:absolute;background:var(--teal);color:var(--white);font-family:"Poppins",sans-serif;font-weight:700;text-transform:uppercase;display:flex;align-items:center;justify-content:center;font-size:12px;letter-spacing:.3px}
.rule{position:absolute;height:2px;background:linear-gradient(90deg,transparent,#222 30%,#222 70%,transparent)}

/* header */
.brand{position:absolute;display:flex;align-items:center;gap:10px;font-family:"Poppins",sans-serif;font-weight:700;font-size:17px;color:var(--ink);letter-spacing:1.5px;text-transform:uppercase}
.contact{position:absolute;display:flex;align-items:center;gap:14px}
.contact .ico{width:30px;height:30px;border:1px solid #333;display:flex;align-items:center;justify-content:center}
.contact small{display:block;font-size:12px;color:#333;text-transform:uppercase}
.contact strong{display:block;font-size:17px;font-weight:400;color:#222}
.nav{position:absolute;display:flex;gap:35px;font-size:15px;text-transform:uppercase;color:#222}
.nav .active{color:var(--teal);font-weight:700}

/* hero */
.hero{left:0;top:115px;width:1200px;height:548px;background:linear-gradient(100deg,#4a3a2a 0%,#a88a63 30%,#3a3028 55%,#8c8478 75%,#d9d6cf 100%)}
.hero::after{content:"";position:absolute;inset:0;background:rgba(0,0,0,.28)}
.hero-copy{position:absolute;left:0;width:1200px;text-align:center;color:var(--white);z-index:2}
.hero-copy h1{font-family:"Poppins",sans-serif;font-weight:800;font-size:58px;line-height:64px;letter-spacing:1px;text-transform:uppercase}
.hero-copy p{font-family:"Poppins",sans-serif;font-weight:700;font-size:19px;line-height:29px;text-transform:uppercase}
.dots{position:absolute;top:614px;left:565px;display:flex;gap:10px;z-index:2}
.dots span{width:10px;height:10px;border-radius:50%;background:var(--white)}
.dots span:first-child{background:var(--teal)}

/* services */
.svc{position:absolute;top:802px;width:297px;height:355px;text-align:center}
.svc::before{content:"";position:absolute;left:0;top:0;right:0;bottom:40px;border-top:1px solid var(--line);border-right:1px solid var(--line);margin-left:10px}
.svc::after{content:"";position:absolute;left:0;top:30px;right:15px;bottom:0;border-left:1px solid var(--line);border-bottom:1px solid var(--line)}
.svc svg{position:absolute;left:112px;top:32px}
.svc h3{position:absolute;left:0;right:0;top:145px;font-family:"Poppins",sans-serif;font-weight:800;font-size:16px;color:var(--ink);line-height:21px;text-transform:uppercase}
.svc p{position:absolute;left:34px;right:34px;font-size:12.5px;line-height:17.5px;color:#555}
.svc .btn{left:96px;width:106px;height:31px}

/* welcome */
.welcome{left:0;top:1200px;width:1200px;height:440px;background:var(--soft)}
.welcome-photo{left:596px;top:1200px;width:604px;height:440px;background:linear-gradient(160deg,#2c2a2e 0%,#1d1c22 40%,#d8d1c4 65%,#3a3438 100%)}
.welcome p{position:absolute;left:133px;top:165px;width:411px;font-size:12.8px;line-height:17.6px;text-align:justify;color:#444}

/* why */
.why{left:0;top:1640px;width:1200px;height:839px;background:linear-gradient(180deg,#f3f2f1,#f7f6f5)}
.photo{position:absolute}
.why-card{position:absolute;top:1942px;height:321px;background:var(--white);border:1px solid #555;text-align:center}
.why-card .badge{position:absolute;top:38px;left:50%;margin-left:-42px;width:84px;height:84px;border-radius:50%;background:var(--teal);display:flex;align-items:center;justify-content:center}
.why-card h3{position:absolute;left:0;right:0;top:150px;font-family:"Poppins",sans-serif;font-weight:800;font-size:16.5px;color:var(--ink);text-transform:uppercase}
.why-card p{position:absolute;left:40px;right:40px;top:186px;font-size:12.8px;line-height:17.5px;color:#555}

/* banner */
.banner{left:0;top:2479px;width:1200px;height:446px;background:linear-gradient(95deg,#5a2e1c 0%,#8a4a2b 30%,#b9a27a 55%,#7a3e22 80%,#4a2616 100%)}
.banner::after{content:"";position:absolute;inset:0;background:linear-gradient(90deg,rgba(0,0,0,.25),rgba(0,0,0,0) 55%)}
.banner-copy{position:absolute;left:144px;z-index:2;color:var(--white)}
.banner-copy h2{font-family:"Poppins",sans-serif;font-weight:800;font-size:34px;line-height:37px;text-transform:uppercase}
.banner-copy p{margin-top:14px;width:330px;font-size:14px;line-height:18px}

/* footer */
.footer{left:0;top:2925px;width:1200px;height:198px;background:var(--footer)}
.footer .brand{color:var(--white)}
.footer .contact .ico{border-color:var(--white);background:var(--white)}
.footer .contact small,.footer .contact strong,.footer .nav{color:var(--white)}
.copyright{position:absolute;left:836px;top:123px;font-size:13px;color:var(--white)}
</style>
</head>
<body>

<!-- header -->
<div class="brand" style="left:133px;top:46px">Northfield Mill Works</div>
<div class="contact" style="left:619px;top:22px">
  <div class="ico"><svg width="16" height="12" viewBox="0 0 16 12"><rect x="1" y="1" width="14" height="10" fill="none" stroke="#222" stroke-width="1.3"/><path d="M1 1l7 6 7-6" fill="none" stroke="#222" stroke-width="1.3"/></svg></div>
  <div><small>Email us</small><strong>info@northfieldmill.com</strong></div>
</div>
<div class="contact" style="left:891px;top:22px">
  <div class="ico"><svg width="16" height="16" viewBox="0 0 16 16"><path d="M3 1l3 3-1.5 2a9 9 0 005 5l2-1.5 3 3-2 2C6 14 2 10 1 3z" fill="#222"/></svg></div>
  <div><small>Call us</small><strong>+1 555 014 2270</strong></div>
</div>
<nav class="nav" style="left:501px;top:78px"><span class="active">Home</span><span>Services we offer</span><span>Capabilities</span><span>About us</span><span>Contact</span></nav>

<!-- hero -->
<div class="abs hero" role="img" aria-label="Modern kitchen with light wood cabinets, dark island and large windows"></div>
<div class="hero-copy" style="top:248px">
  <h1>Wood cabinet</h1>
  <p style="margin-top:22px">Lorem ipsum dolor sit amet, consectetur adipiscing elit<br>sed do eiusmod tempor incididunt ut labore</p>
</div>
<div class="btn" style="left:520px;top:404px;width:160px;height:47px;font-size:18px;z-index:2">Read more</div>
<div class="dots"><span></span><span></span><span></span><span></span></div>

<!-- services -->
<h2 class="abs heading" style="left:0;width:1200px;top:696px;text-align:center;font-size:32px">Services we offer</h2>
<div class="rule" style="left:498px;top:758px;width:206px"></div>

<div class="svc" style="left:131px">
  <svg width="70" height="80" viewBox="0 0 70 80" fill="none" stroke="#17a2c2" stroke-width="3"><circle cx="35" cy="35" r="24" stroke-dasharray="9 5"/><circle cx="35" cy="35" r="15"/><path d="M30 38l5-14 5 14v28h-10z"/></svg>
  <h3>Design engineering</h3>
  <p style="top:180px">Sed ut perspiciatis unde omnis iste natus error sit voluptatem accus antium doloremque laudantium, totam rem aperiam, eaque ipsa quae ab illo inventore veritatis</p>
  <div class="btn" style="top:286px">Read more</div>
</div>
<div class="svc" style="left:450px">
  <svg width="80" height="80" viewBox="0 0 80 80" fill="none" stroke="#17a2c2" stroke-width="3"><rect x="20" y="10" width="38" height="50" rx="3"/><rect x="30" y="28" width="18" height="16" fill="#17a2c2"/><path d="M6 40l10 28M74 40l-10 28"/><circle cx="62" cy="10" r="6"/></svg>
  <h3>Product development<br>prototype</h3>
  <p style="top:200px">Sed ut perspiciatis unde omnis iste natus error sit voluptatem accus antium doloremque laudantium, totam rem aperiam, eaque ipsa.</p>
  <div class="btn" style="top:286px">Read more</div>
</div>
<div class="svc" style="left:768px">
  <svg width="80" height="80" viewBox="0 0 80 80" fill="none" stroke="#17a2c2" stroke-width="3"><rect x="10" y="24" width="62" height="46" rx="2"/><path d="M22 30h38M41 30v14l-6 8h12l-6-8"/><circle cx="10" cy="10" r="3"/><circle cx="52" cy="8" r="3"/><circle cx="68" cy="10" r="4"/><text x="46" y="58" font-family="Poppins,sans-serif" font-size="13" font-weight="700" fill="#17a2c2" stroke="none">3D</text></svg>
  <h3>3D printing</h3>
  <p style="top:180px">Sed ut perspiciatis unde omnis iste natus error sit voluptatem accus antium doloremque laudantium, totam rem aperiam, eaque ipsa quae ab illo inventore veritatis</p>
  <div class="btn" style="top:286px">Read more</div>
</div>

<!-- welcome -->
<section class="abs welcome">
  <h2 class="abs heading" style="left:133px;top:45px;font-size:32px;line-height:39px">Welcome to<br>Northfield Mill Works</h2>
  <div class="rule" style="left:140px;top:136px;width:214px"></div>
  <p>Sed ut perspiciatis unde omnis iste natus error sit voluptatem accusantium doloremque laudantium, totam rem aperiam, eaque ipsa quae ab illo inventore veritatis et quasi architecto beatae vitae dicta sunt explicabo. Nemo enim ipsam voluptatem quia voluptas sit aspernatur aut odit aut fugit, sed quia consequuntur magni dolores eos qui ratione voluptatem sequi nesciunt. Neque porro quisquam est, qui dolorem ipsum quia dolor sit amet, consectetur, adipisci velit, sed quia non numquam eius modi tempora incidunt ut labore et dolore magnam aliquam quaerat voluptatem</p>
  <div class="btn" style="left:133px;top:352px;width:106px;height:31px">Read more</div>
</section>
<div class="abs welcome-photo" role="img" aria-label="Kitchen with dark navy cabinets, white countertops and window view"></div>

<!-- why choose us -->
<section class="abs why">
  <h2 class="abs heading" style="left:0;width:1200px;top:40px;text-align:center;font-size:32px">Why choose us</h2>
  <div class="rule" style="left:498px;top:100px;width:206px"></div>
</section>
<div class="photo" style="left:131px;top:1778px;width:315px;height:164px;background:linear-gradient(120deg,#6b3e22,#a66a3e,#c9c5c0)" role="img" aria-label="Walnut cabinetry with wire drawer baskets"></div>
<div class="photo" style="left:446px;top:1778px;width:301px;height:164px;background:linear-gradient(100deg,#8a8886,#c9c6c2,#1c1c1c 60%,#f0ece6)" role="img" aria-label="Glossy grey and white kitchen cabinets"></div>
<div class="photo" style="left:747px;top:1778px;width:320px;height:164px;background:linear-gradient(100deg,#b9b5b0,#7a4a2a 45%,#a06a40,#cfd0d2)" role="img" aria-label="Granite counter and wood open shelving"></div>

<div class="why-card" style="left:131px;width:316px">
  <div class="badge"><svg width="50" height="40" viewBox="0 0 50 40" fill="none" stroke="#fff" stroke-width="3.5" stroke-linecap="round" stroke-linejoin="round"><path d="M3 16l9-8 8 4 8-4 9 8M12 8L3 20M38 8l9 12M14 22l7 6 6-2 6 4 6-6-10-10-6 4"/></svg></div>
  <h3>Communicate trust</h3>
  <p>Sed ut perspiciatis unde omnis iste natus error sit voluptatem accus antium doloremque laudantium, totam rem aperiam, eaque ipsa quae ab illo inventore veritatis</p>
</div>
<div class="why-card" style="left:446px;width:302px">
  <div class="badge"><svg width="50" height="46" viewBox="0 0 50 46" fill="none" stroke="#fff" stroke-width="3" stroke-linejoin="round"><path d="M16 6h18l6 7-15 15-15-15z"/><path d="M4 36h10l10 4 14-6 8-4" stroke-linecap="round"/></svg></div>
  <h3>Dependability</h3>
  <p>Sed ut perspiciatis unde omnis iste natus error sit voluptatem accus antium doloremque laudantium, totam rem aperiam, eaque ipsa quae ab illo inventore veritatis</p>
</div>
<div class="why-card" style="left:747px;width:320px">
  <div class="badge"><svg width="46" height="46" viewBox="0 0 46 46" fill="#fff"><circle cx="23" cy="19" r="14"/><rect x="14" y="28" width="16" height="14"/><path d="M23 25l-6-6a3.5 3.5 0 016-4 3.5 3.5 0 016 4z" fill="#17a2c2"/></svg></div>
  <h3>The value</h3>
  <p>Sed ut perspiciatis unde omnis iste natus error sit voluptatem accus antium doloremque laudantium, totam rem aperiam, eaque ipsa quae ab illo inventore veritatis</p>
</div>

<div class="photo" style="left:131px;top:2263px;width:316px;height:162px;background:linear-gradient(110deg,#b08656,#2a2624 40%,#c8b08c 70%,#e9e3da)" role="img" aria-label="Light oak kitchen with island and bar stools"></div>
<div class="photo" style="left:447px;top:2263px;width:301px;height:162px;background:linear-gradient(135deg,#3a1e10,#8a4a22 45%,#5a2e16)" role="img" aria-label="Close-up of cherry wood drawers with round knobs"></div>
<div class="photo" style="left:748px;top:2263px;width:320px;height:162px;background:linear-gradient(100deg,#d9dcc4,#e8e6d8 50%,#f4f2ee)" role="img" aria-label="Pale sage kitchen cabinets with microwave"></div>

<!-- banner -->
<div class="abs banner" role="img" aria-label="Traditional kitchen with cherry wood cabinets, granite counters and arched window"></div>
<div class="banner-copy" style="top:2580px">
  <h2>Custom<br>manufacturing<br>company</h2>
  <p>Sed ut perspiciatis unde omnis iste natus error sit voluptatem accus antium doloremque lauda ntium, totam rem aperiam, eaque ipsa quae ab illo inventore veritatis</p>
</div>
<div class="btn" style="left:147px;top:2797px;width:106px;height:31px;z-index:2">Read more</div>

<!-- footer -->
<footer class="abs footer">
  <div class="brand" style="left:133px;top:88px;font-size:18px">Northfield Mill Works</div>
  <div class="contact" style="left:616px;top:35px">
    <div class="ico"><svg width="16" height="12" viewBox="0 0 16 12"><rect x="1" y="1" width="14" height="10" fill="none" stroke="#222" stroke-width="1.3"/><path d="M1 1l7 6 7-6" fill="none" stroke="#222" stroke-width="1.3"/></svg></div>
    <div><small>Email us</small><strong>info@northfieldmill.com</strong></div>
  </div>
  <div class="contact" style="left:888px;top:35px">
    <div class="ico"><svg width="16" height="16" viewBox="0 0 16 16"><path d="M3 1l3 3-1.5 2a9 9 0 005 5l2-1.5 3 3-2 2C6 14 2 10 1 3z" fill="#222"/></svg></div>
    <div><small>Call us</small><strong>+1 555 014 2270</strong></div>
  </div>
  <nav class="nav" style="left:502px;top:88px"><span>Home</span><span>Services we offer</span><span>Capabilities</span><span>About us</span><span>Contact</span></nav>
  <div class="copyright">Copyright © 2023 All Rights Reserved</div>
</footer>

</body>
</html>
```